Tidewell-Network Theme For Forums!

We are looking for a theme for our forums. The forums are ran off Invision Power Boards. We have a basic theme on there now but we want more our own feel. If possible have some longboarding accept incorporated in the theme. We want the theme to have some red in it to match our logo. Tidewell-network.com

Target Market(s)

Skatingboarding & Longboarding

Coding

Coded - Design and coding required

Number of Pages Required

1 page

Colors
f04a50

```html
<!DOCTYPE html>
<html lang="en">
<head>
<meta charset="utf-8">
<title>Tidewell Network Forums</title>
<link href="https://fonts.googleapis.com/css2?family=Montserrat:wght@400;500;600;700;800&display=swap" rel="stylesheet">
<style>
:root{
  --red:#f04a50;
  --red-dark:#d8333a;
  --pink:#fde8e8;
  --pink-mid:#fcd9da;
  --row-grey:#f2f2f2;
  --text:#222;
  --border:#cfcfcf;
}
*{box-sizing:border-box;margin:0;padding:0}
html,body{width:1062px;height:1200px;overflow:hidden;background:#fff;font-family:'Montserrat',sans-serif;color:var(--text)}
.page{position:relative;width:1062px;height:1200px}
.masthead{position:absolute;left:17px;top:10px;width:1001px;height:84px;background:linear-gradient(180deg,#f25a5f,var(--red-dark))}
.brand{position:absolute;left:24px;top:27px;display:flex;align-items:center;gap:10px;color:#fff;font-weight:800;font-size:25px;letter-spacing:1px;text-transform:uppercase}
.brand-dot{width:16px;height:16px;background:#fff}
.avatar{position:absolute;left:716px;top:11px;width:72px;height:57px;background:linear-gradient(135deg,#8a7a6a,#c9b6a2);border:2px solid #fff}
.user-select{position:absolute;top:19px;height:20px;background:rgba(160,20,25,.45);color:#fff;font-size:10px;padding:3px 7px;border-radius:2px}
.user-select::after{content:"";position:absolute;right:7px;top:8px;border:3.5px solid transparent;border-top-color:#fff}
.user-links{position:absolute;left:799px;top:48px;display:flex;gap:16px;font-size:11px;font-weight:600;color:#fff;text-decoration:underline}
.navbar{position:absolute;left:17px;top:97px;width:1001px;height:31px;background:var(--red);display:flex;align-items:center}
.navbar a{color:#fff;font-weight:600;font-size:12.5px;text-decoration:none;margin-left:13px;margin-right:21px}
.nav-search{position:absolute;left:686px;top:5px;width:274px;height:21px;background:#fff;border-radius:2px;font-size:10.5px;display:flex;align-items:center}
.nav-search .field{flex:1;padding-left:7px;border-right:1px solid #333;height:15px;line-height:15px}
.nav-search .scope{width:83px;padding-left:6px;position:relative}
.nav-search .scope::after{content:"";position:absolute;right:10px;top:5px;border:3.5px solid transparent;border-top-color:#333}
.search-btn{position:absolute;left:965px;top:5px;width:26px;height:21px;background:var(--red-dark);border-radius:2px}
.welcome{position:absolute;left:17px;top:134px;width:1001px;height:41px;background:var(--pink);text-align:center;font-size:19px;font-weight:700;color:var(--red-dark);line-height:41px}
.crumb{position:absolute;left:17px;top:204px;font-size:12px;display:flex;align-items:center;gap:7px}
.crumb::before{content:"";border:4px solid transparent;border-left:5px solid #333;border-right:0}
.pager{position:absolute;left:16px;top:245px;display:flex;align-items:center;font-size:12.5px}
.pager .count{margin-right:12px}
.pager .pg{border:1px solid #333;height:16px;min-width:20px;padding:0 4px;text-align:center;font-size:11px;line-height:14px;margin-right:5px}
.pager .pg.current{border-color:#ddd;background:#eee}
.pager .pg.last{margin-left:4px;font-size:9.5px;min-width:34px}
.btn{position:absolute;top:238px;height:32px;border-radius:3px;font-size:12.5px;line-height:32px;text-align:center}
.btn-watch{left:815px;width:91px;background:var(--red);color:#fff}
.btn-new{left:915px;width:104px;background:#f0f0f0;border:1px solid #bbb;line-height:30px}
.forum{position:absolute;left:17px;top:296px;width:1001px}
.forum-title{height:34px;background:var(--red);color:#fff;font-size:13px;font-weight:500;display:flex;justify-content:space-between;align-items:center;padding:0 10px}
.forum-title small{font-size:11.5px}
.group{height:31px;background:var(--pink-mid);font-size:12px;font-weight:500;line-height:31px;padding-left:9px}
.grid{display:grid;grid-template-columns:35px 362px 88px 202px 253px 61px}
.colhead{height:30px;background:var(--pink);font-size:11px;font-weight:500;align-items:center}
.colhead div:nth-child(3){text-align:center}
.colhead div:nth-child(4){padding-left:75px}
.colhead div:nth-child(5){padding-left:15px}
.row{height:56px;font-size:11px}
.row>div{padding-top:12px}
.row.odd>div:nth-child(odd){background:var(--row-grey)}
.row.odd>div:nth-child(even){background:#fff}
.row.even>div{background:var(--row-grey)}
.icon{display:flex;justify-content:center;padding-top:20px!important}
.topic{padding-left:10px}
.topic .title{display:flex;align-items:center;gap:8px;font-size:11.5px;font-weight:500}
.tag{background:var(--red);color:#fff;font-size:8.5px;padding:2px 7px;border-radius:2px}
.topic .sub{font-size:9px;margin-top:6px;font-weight:500}
.starter{text-align:center;padding-top:18px!important}
.stats{padding-left:75px;padding-top:17px!important;line-height:14px}
.lastpost{padding-left:15px;padding-top:17px!important;line-height:14px}
.box{width:13px;height:13px;border:1px solid #ccc;background:#fff;margin:0 auto}
.check{padding-top:23px!important}
.colhead .check{padding-top:0!important}
.footer-links{position:absolute;left:17px;top:939px;width:1001px;height:36px;background:var(--red);display:flex;justify-content:center;align-items:center;gap:15px;color:#fff;font-size:12px;font-weight:500}
.board-info{position:absolute;left:17px;top:975px;width:1001px;height:141px;border:1px solid #ccc;border-top:0}
.info-head{position:absolute;display:flex;align-items:center;gap:8px;font-size:13.5px;font-weight:500}
.info-text{position:absolute;font-size:11px;font-weight:500;line-height:21px}
.info-text .member{color:var(--red)}
.stat-table{position:absolute;left:573px;top:66px;font-size:11px;font-weight:500;line-height:21px}
.stat-table div{display:flex}
.stat-table span:first-child{width:184px}
.rule{position:absolute;left:17px;top:1148px;width:1028px;height:1px;background:#ddd}
.copyright{position:absolute;left:0;top:1168px;width:1062px;text-align:center;font-size:12px;font-weight:500}
</style>
</head>
<body>
<div class="page">
  <header class="masthead">
    <div class="brand"><span class="brand-dot"></span>Tidewell Network</div>
    <div class="avatar" role="img" aria-label="Member profile photo"></div>
    <div class="user-select" style="left:799px;width:129px">tvrn</div>
    <div class="user-select" style="left:934px;width:58px">0</div>
    <div class="user-links"><span>SignOut</span><span>Help</span></div>
  </header>

  <nav class="navbar">
    <a>Help</a><a>Search</a><a>Members</a><a>Calendar</a>
    <div class="nav-search"><div class="field">Search</div><div class="scope">This Forum</div></div>
    <div class="search-btn">
      <svg width="26" height="21" viewBox="0 0 26 21"><circle cx="12" cy="9.5" r="3.5" fill="none" stroke="#fff" stroke-width="1.6"/><line x1="14.5" y1="12" x2="17" y2="14.5" stroke="#fff" stroke-width="1.8"/></svg>
    </div>
  </nav>

  <div class="welcome">Welcome Guest!</div>
  <div class="crumb">Tidewell Network</div>

  <div class="pager">
    <span class="count">(50 Pages)</span>
    <span class="pg current">1</span><span class="pg">2</span><span class="pg">3</span>
    <span class="pg"><svg width="10" height="10" viewBox="0 0 10 10"><path d="M1 5h7M5 2l3 3-3 3" stroke="#222" stroke-width="1.6" fill="none"/></svg></span>
    <span class="pg last">Last</span>
  </div>
  <div class="btn btn-watch">Watch Forum</div>
  <div class="btn btn-new">Start New Topic</div>

  <section class="forum">
    <div class="forum-title"><span>Nemo enim ipsam voluptatem</span><small>(Mark this forum as read)</small></div>

    <div class="group">Important Topics</div>
    <div class="grid colhead"><div></div><div style="padding-left:10px">Topics</div><div>Started By</div><div>Stats</div><div>Last Post Info</div><div class="check"><div class="box"></div></div></div>

    <div class="grid row odd">
      <div class="icon"><svg width="18" height="14" viewBox="0 0 18 14"><path d="M0 2h6l2 2h7v2H4L0 13z M1 14l4-7h13l-4 7z" fill="#222"/></svg></div>
      <div class="topic"><div class="title"><span class="tag">Pinned</span>Serving The Filler Of A Corvane Deluxe Ridged</div><div class="sub">a guide with pictures...</div></div>
      <div class="starter">reno214</div>
      <div class="stats">1 Reply<br>95 Views</div>
      <div class="lastpost">➔ Today, 01:31 PM<br>By: dellowr</div>
      <div class="check"><div class="box"></div></div>
    </div>
    <div class="grid row even">
      <div class="icon"><svg width="18" height="14" viewBox="0 0 18 14"><path d="M0 2h6l2 2h7v2H4L0 13z M1 14l4-7h13l-4 7z" fill="#222"/></svg></div>
      <div class="topic"><div class="title"><span class="tag">Pinned</span>Italian Brands Contact Info</div><div class="sub">a guide with pictures...</div></div>
      <div class="starter">skatelass9</div>
      <div class="stats">1 Reply<br>95 Views</div>
      <div class="lastpost">➔Apr 21 2018 03:12 PM<br>By: dellowr</div>
      <div class="check"><div class="box"></div></div>
    </div>
    <div class="grid row odd">
      <div class="icon"><svg width="18" height="14" viewBox="0 0 18 14"><path d="M0 2h6l2 2h7v2H4L0 13z M1 14l4-7h13l-4 7z" fill="#222"/></svg></div>
      <div class="topic"><div class="title"><span class="tag">Pinned</span>Serving The Filler Of A Corvane Deluxe Ridged</div><div class="sub">a guide with pictures...</div></div>
      <div class="starter">reno214</div>
      <div class="stats">1 Reply<br>95 Views</div>
      <div class="lastpost">➔ Today, 01:31 PM<br>By: dellowr</div>
      <div class="check"><div class="box"></div></div>
    </div>
    <div class="grid row even">
      <div class="icon"><svg width="18" height="14" viewBox="0 0 18 14"><path d="M0 2h6l2 2h7v2H4L0 13z M1 14l4-7h13l-4 7z" fill="#222"/></svg></div>
      <div class="topic"><div class="title"><span class="tag">Pinned</span>Italian Brands Contact Info</div><div class="sub">a guide with pictures...</div></div>
      <div class="starter">skatelass9</div>
      <div class="stats">1 Reply<br>95 Views</div>
      <div class="lastpost">➔Apr 21 2018 03:12 PM<br>By: dellowr</div>
      <div class="check"><div class="box"></div></div>
    </div>

    <div class="group">Forum Topics</div>
    <div class="grid colhead"><div></div><div style="padding-left:10px">Topics</div><div>Started By</div><div>Stats</div><div>Last Post Info</div><div class="check"><div class="box"></div></div></div>

    <div class="grid row odd">
      <div class="icon"><svg width="18" height="14" viewBox="0 0 18 14"><path d="M0 2h6l2 2h7v2H4L0 13z M1 14l4-7h13l-4 7z" fill="#222"/></svg></div>
      <div class="topic"><div class="title"><span class="tag">Pinned</span>Serving The Filler Of A Corvane Deluxe Ridged</div><div class="sub">a guide with pictures...</div></div>
      <div class="starter">reno214</div>
      <div class="stats">1 Reply<br>95 Views</div>
      <div class="lastpost">➔ Today, 01:31 PM<br>By: dellowr</div>
      <div class="check"><div class="box"></div></div>
    </div>
    <div class="grid row even">
      <div class="icon"><svg width="18" height="14" viewBox="0 0 18 14"><path d="M0 2h6l2 2h7v2H4L0 13z M1 14l4-7h13l-4 7z" fill="#222"/></svg></div>
      <div class="topic"><div class="title"><span class="tag">Pinned</span>Italian Brands Contact Info</div><div class="sub">a guide with pictures...</div></div>
      <div class="starter">skatelass9</div>
      <div class="stats">1 Reply<br>95 Views</div>
      <div class="lastpost">➔Apr 21 2018 03:12 PM<br>By: dellowr</div>
      <div class="check"><div class="box"></div></div>
    </div>
    <div class="grid row odd">
      <div class="icon"><svg width="18" height="14" viewBox="0 0 18 14"><path d="M0 2h6l2 2h7v2H4L0 13z M1 14l4-7h13l-4 7z" fill="#222"/></svg></div>
      <div class="topic"><div class="title"><span class="tag">Pinned</span>Serving The Filler Of A Corvane Deluxe Ridged</div><div class="sub">a guide with pictures...</div></div>
      <div class="starter">reno214</div>
      <div class="stats">1 Reply<br>95 Views</div>
      <div class="lastpost">➔ Today, 01:31 PM<br>By: dellowr</div>
      <div class="check"><div class="box"></div></div>
    </div>
    <div class="grid row even">
      <div class="icon"><svg width="18" height="14" viewBox="0 0 18 14"><path d="M0 2h6l2 2h7v2H4L0 13z M1 14l4-7h13l-4 7z" fill="#222"/></svg></div>
      <div class="topic"><div class="title"><span class="tag">Pinned</span>Italian Brands Contact Info</div><div class="sub">a guide with pictures...</div></div>
      <div class="starter">skatelass9</div>
      <div class="stats">1 Reply<br>95 Views</div>
      <div class="lastpost">➔Apr 21 2018 03:12 PM<br>By: dellowr</div>
      <div class="check"><div class="box"></div></div>
    </div>
  </section>

  <div class="footer-links"><span>Today's active content</span><span>The moderating team</span><span>Today's top 20 posters</span><span>Overall top posters</span></div>

  <section class="board-info">
    <div class="info-head" style="left:29px;top:37px">
      <svg width="28" height="28" viewBox="0 0 28 28"><circle cx="14" cy="14" r="12.5" fill="none" stroke="#222" stroke-width="2"/><circle cx="14" cy="11" r="4.5" fill="none" stroke="#222" stroke-width="2"/><path d="M6 23c2-5 14-5 16 0" fill="none" stroke="#222" stroke-width="2"/></svg>
      20 active user(s) (in the past 15 minutes)
    </div>
    <div class="info-text" style="left:30px;top:66px">1 members, 19 guests, 0 anonymous users &nbsp;| &nbsp;Show by: Last Click or Member Name<br><span class="member">Marcus,</span> Searchbot</div>
    <div class="info-head" style="left:573px;top:37px">
      <svg width="30" height="26" viewBox="0 0 30 26"><path d="M1 1v24h28" fill="none" stroke="#222" stroke-width="2"/><rect x="6" y="13" width="2.5" height="9" fill="#222"/><rect x="11" y="8" width="2.5" height="14" fill="#222"/><rect x="16" y="15" width="2.5" height="7" fill="#222"/><rect x="21" y="10" width="2.5" height="12" fill="#222"/></svg>
      Our Board Statistics
    </div>
    <div class="stat-table"><div><span>Total Posts</span><span>16</span></div><div><span>Total Members</span><span>4</span></div></div>
  </section>

  <div class="rule"></div>
  <div class="copyright">Copyrights @ 2018 Tidewell Network. All Rights Reserved.</div>
</div>
</body>
</html>
```